Harcourt Power Gym Chronic Pain Flyer

Double sided DL flyer required to promote a strength training studio to sufferers of chronic pain. Flyer will be displayed in osteopathy, chiropractic and massage clinics. Flyer should be clean, professional and appeal to an older (40+) demographic.

Target Market(s)

Chronic pain sufferers. Age 40+

Industry/Entity Type

Health And Wellness

Colors

Designer to choose colors to be used in the design.

Requirements
Must have
• See attached files for text copy and logo. Image(s) of people strength training with a coach or personal trainer, as well as images depicting pain in common parts of the body (such as those pictured in the supplied mock up)
• website address: harcourtpowergym.com.au
• phone number : 0458 214 963
• Street address: 3/14 Birchwood Rd, Harcourt
Nice to have
• Images such as in the attached files.

```html
<!DOCTYPE html>
<html lang="en">
<head>
<meta charset="utf-8">
<title>Harcourt Power Gym – Chronic Pain DL Flyer</title>
<link rel="stylesheet" href="https://fonts.googleapis.com/css2?family=Jost:wght@400;500&family=Montserrat:wght@400;500;600;700;900&display=swap">
<style>
  :root {
    --page-bg: #efefef;
    --panel-dark: #232323;
    --brand-red: #d7262b;
    --brand-red-deep: #a8181c;
    --text-light: #ffffff;
    --text-silver: #e4e4e4;
    --text-dark: #111111;
    --photo-light: #f2f2f2;
    --photo-pain: #e0707a;
  }
  * { box-sizing: border-box; margin: 0; padding: 0; }
  html, body { width: 1200px; height: 1200px; overflow: hidden; background: var(--page-bg); }
  body { position: relative; font-family: "Montserrat", sans-serif; }

  .flyer {
    position: absolute; top: 242px; width: 344px; height: 728px;
    overflow: hidden; background: var(--panel-dark);
  }
  .flyer--front { left: 234px; }
  .flyer--back { left: 638px; }

  .flyer__photo { position: absolute; left: 0; top: 0; width: 344px; height: 360px; }
  .flyer--front .flyer__photo {
    background:
      radial-gradient(circle at 52% 55%, var(--photo-pain) 0, rgba(224,112,122,0) 70px),
      linear-gradient(160deg, #8d8d8d 0%, #d8d8d8 45%, #f4f4f4 100%);
  }
  .flyer--back .flyer__photo {
    background:
      radial-gradient(circle at 78% 62%, #e4454a 0, rgba(228,69,74,0) 90px),
      linear-gradient(90deg, var(--photo-light) 0%, #e6e6e6 55%, #a9a9a9 100%);
  }
  .flyer__curve { position: absolute; left: 0; top: 0; width: 344px; height: 728px; }

  .centered { position: absolute; left: 0; width: 100%; text-align: center; }

  .brand-name {
    font-family: "Montserrat", sans-serif; font-weight: 700;
    text-transform: uppercase; letter-spacing: 1px;
  }
  .flyer--front .brand-name { top: 382px; font-size: 22px; color: var(--text-silver); }
  .flyer--back .brand-name {
    position: absolute; left: 16px; top: 76px; font-size: 19px; color: var(--text-dark);
    line-height: 1.1;
  }

  .headline-light {
    top: 460px; font-family: "Jost", sans-serif; font-weight: 400;
    font-size: 50px; line-height: 38px; color: var(--text-silver); letter-spacing: 0.5px;
  }

  .divider {
    position: absolute; left: 44px; width: 256px; top: 602px; height: 1px;
    background: linear-gradient(90deg, rgba(255,255,255,0), #6a6a6a, rgba(255,255,255,0));
  }

  .contact-phone {
    display: flex; align-items: center; justify-content: center; gap: 4px;
    color: var(--text-light);
  }
  .contact-phone svg, .contact-address svg { flex: none; }
  .flyer--front .contact-phone { top: 608px; font-family: "Jost", sans-serif; font-size: 26px; font-weight: 400; }
  .flyer--back .contact-phone { top: 598px; font-size: 25px; font-weight: 700; }

  .contact-address {
    display: flex; justify-content: center; gap: 6px;
    color: var(--text-light); font-size: 16px; line-height: 19px;
  }
  .flyer--front .contact-address { top: 642px; font-family: "Jost", sans-serif; font-weight: 500; }
  .flyer--back .contact-address { top: 632px; font-family: "Jost", sans-serif; font-weight: 400; font-size: 17px; }
  .contact-address svg { margin-top: 2px; }

  .web-bar {
    position: absolute; left: 0; bottom: 0; width: 100%; height: 32px;
    background: linear-gradient(90deg, var(--brand-red-deep), var(--brand-red), var(--brand-red-deep));
    color: var(--text-light); font-size: 16.5px; line-height: 32px; text-align: center;
  }
  .web-bar b { font-weight: 700; }
  .web-bar span { font-weight: 400; }

  .headline-bold {
    position: absolute; left: 20px; top: 184px;
    font-weight: 900; font-size: 31px; line-height: 29px; color: var(--text-dark);
    text-transform: uppercase;
  }
  .tagline {
    position: absolute; left: 22px; top: 275px;
    font-weight: 700; font-size: 14.5px; line-height: 17px; color: var(--brand-red);
    text-transform: uppercase; letter-spacing: 0.3px;
  }

  .body-copy {
    font-size: 11.8px; line-height: 14.6px;
    font-weight: 500; color: var(--text-light);
  }
  .body-copy--one { top: 363px; left: 40px; width: 264px; }
  .body-copy--two { top: 435px; left: 24px; width: 296px; }
  .body-copy--three { top: 479px; left: 32px; width: 280px; }

  .call-to-action {
    top: 522px; font-weight: 900; font-size: 14.5px; line-height: 14.5px;
    color: var(--brand-red); text-transform: uppercase;
  }
</style>
</head>
<body>

  <section class="flyer flyer--front">
    <div class="flyer__photo" role="img" aria-label="Black and white photo of a man holding his painful shoulder, highlighted in red"></div>
    <svg class="flyer__curve" viewBox="0 0 344 728" aria-hidden="true">
      <path d="M0 338 Q170 292 344 328 L344 728 L0 728 Z" fill="var(--panel-dark)"/>
    </svg>

    <div class="centered brand-name">Harcourt Power Gym</div>

    <h1 class="centered headline-light">HEALTH<br>THROUGH<br>STRENGTH</h1>

    <div class="divider"></div>

    <div class="centered contact-phone">
      <svg width="20" height="20" viewBox="0 0 24 24"><path fill="var(--brand-red)" d="M6.6 10.8a15.1 15.1 0 0 0 6.6 6.6l2.2-2.2a1 1 0 0 1 1-.25 11.4 11.4 0 0 0 3.6.57 1 1 0 0 1 1 1V20a1 1 0 0 1-1 1A17 17 0 0 1 3 4a1 1 0 0 1 1-1h3.5a1 1 0 0 1 1 1c0 1.25.2 2.45.57 3.57a1 1 0 0 1-.25 1z"/></svg>
      0458 214 963
    </div>
    <div class="centered contact-address">
      <svg width="14" height="18" viewBox="0 0 14 18"><path fill="none" stroke="var(--brand-red)" stroke-width="2.2" d="M7 16.5S1.5 10.5 1.5 6.6a5.5 5.5 0 0 1 11 0C12.5 10.5 7 16.5 7 16.5z"/><circle cx="7" cy="6.6" r="1.8" fill="var(--brand-red)"/></svg>
      <span>3/14 Birchwood Rd,<br>Harcourt, VIC, 3453</span>
    </div>

    <div class="web-bar"><b>harcourtpowergym</b><span>.com.au</span></div>
  </section>

  <section class="flyer flyer--back">
    <div class="flyer__photo" role="img" aria-label="Black and white photo of hands clasping a painful knee, highlighted in red"></div>
    <svg class="flyer__curve" viewBox="0 0 344 728" aria-hidden="true">
      <path d="M0 348 Q170 300 344 344 L344 728 L0 728 Z" fill="var(--panel-dark)"/>
    </svg>

    <div class="brand-name">Harcourt<br>Power Gym</div>

    <h2 class="headline-bold">Health<br>Through<br>Strength</h2>
    <p class="tagline">You don’t have to<br>live in pain</p>

    <p class="centered body-copy body-copy--one">strength training has been shown to improve many chronic pain conditions and is now being routinely recommended by medical and health professionals.</p>
    <p class="centered body-copy body-copy--two">Our private studio provides high quality strength training by expert strength coaches.</p>
    <p class="centered body-copy body-copy--three">We’ve helped countless people improve or eliminate chronic pain.</p>

    <p class="centered call-to-action">Contact us today and<br>find out how<br>we can help you.</p>

    <div class="centered contact-phone">
      <svg width="22" height="22" viewBox="0 0 24 24"><path fill="var(--brand-red)" d="M6.6 10.8a15.1 15.1 0 0 0 6.6 6.6l2.2-2.2a1 1 0 0 1 1-.25 11.4 11.4 0 0 0 3.6.57 1 1 0 0 1 1 1V20a1 1 0 0 1-1 1A17 17 0 0 1 3 4a1 1 0 0 1 1-1h3.5a1 1 0 0 1 1 1c0 1.25.2 2.45.57 3.57a1 1 0 0 1-.25 1z"/></svg>
      0458 214 963
    </div>
    <div class="centered contact-address">
      <svg width="14" height="18" viewBox="0 0 14 18"><path fill="none" stroke="var(--brand-red)" stroke-width="2.2" d="M7 16.5S1.5 10.5 1.5 6.6a5.5 5.5 0 0 1 11 0C12.5 10.5 7 16.5 7 16.5z"/><circle cx="7" cy="6.6" r="1.8" fill="var(--brand-red)"/></svg>
      <span>3/14 Birchwood Rd,<br>Harcourt, VIC, 3453</span>
    </div>

    <div class="web-bar"><b>harcourtpowergym</b><span>.com.au</span></div>
  </section>

</body>
</html>
```